Computer consultant business card

Trelvo Software is a newly started computer consulting company. It's a small one-man company that provides mostly Vornix applications but also websites in collaboration with designers. I'm running this company on the side of full time university studies.

I want the final design to be clean and memorable. Be creative! :)

Some inspiration:
http://www.pixelmarta.com/design/48317
http://www.pixelmarta.com/design/2739164/business-card-design-by-frostlynk
http://www.pixelmarta.com/design/604281/business-card-design-by-koralind-vestrabanu

See attachment for my company logo.
Updates

I would like to thank everyone for submitting! I'll need a couple of days to review and ultimately select a design.

Target Market(s)

Non-technical entrepreneurs and small companies.

Industry/Entity Type

University

Requirements
Must have
• My company logo.
In any way, both colors from my logo.
First- and last name, e-mail and phone number.
Double-sided design.
Nice to have
• Something creative with the symbol in my logo

```html
<!DOCTYPE html>
<html lang="en">
<head>
<meta charset="utf-8">
<title>Trelvo Software – Business Card</title>
<link rel="stylesheet" href="https://fonts.googleapis.com/css2?family=Maven+Pro:wght@400;500&display=swap">
<style>
  :root {
    --canvas: #e9ecef;
    --card-white: #ffffff;
    --ink-dark: #3a3a3c;
    --brand-blue: #2a7de1;
    --back-deep: #2a64b8;
    --back-light: #1ba2d4;
    --shadow: rgba(20, 40, 60, 0.18);
  }
  * { box-sizing: border-box; margin: 0; padding: 0; }
  html, body {
    width: 1200px;
    height: 960px;
    overflow: hidden;
    background: var(--canvas);
    font-family: "Maven Pro", sans-serif;
  }
  .canvas {
    width: 1200px;
    height: 960px;
    display: flex;
    flex-direction: column;
    align-items: center;
    justify-content: center;
    gap: 40px;
  }
  .card {
    width: 700px;
    height: 400px;
    position: relative;
    box-shadow: 0 10px 30px var(--shadow);
  }

  /* Front side */
  .card-front { background: var(--card-white); }
  .brand-lockup {
    position: absolute;
    top: 78px;
    left: 0;
    right: 0;
    display: flex;
    align-items: center;
    justify-content: center;
    gap: 26px;
  }
  .brand-dot {
    width: 92px;
    height: 92px;
    border-radius: 50%;
    background: var(--brand-blue);
    flex: none;
  }
  .brand-name {
    font-size: 88px;
    font-weight: 500;
    color: var(--ink-dark);
    letter-spacing: 1px;
    line-height: 1;
  }
  .holder-name {
    position: absolute;
    top: 232px;
    left: 300px;
    font-size: 27px;
    font-weight: 400;
    letter-spacing: 1.5px;
    color: var(--ink-dark);
    white-space: nowrap;
  }
  .contact {
    position: absolute;
    top: 296px;
    left: 300px;
    display: flex;
    gap: 10px;
    font-size: 17px;
    line-height: 1.3;
    white-space: nowrap;
  }
  .contact-labels {
    color: var(--brand-blue);
    padding-right: 8px;
    border-right: 1.5px solid var(--brand-blue);
    text-align: center;
  }
  .contact-values { color: var(--ink-dark); }

  /* Back side */
  .card-back {
    background: linear-gradient(160deg, var(--back-deep) 0%, var(--back-light) 55%, var(--back-deep) 100%);
  }
  .back-mark {
    position: absolute;
    right: 36px;
    bottom: 30px;
    display: flex;
    align-items: center;
    gap: 14px;
  }
  .back-dot {
    width: 54px;
    height: 54px;
    border-radius: 50%;
    background: var(--card-white);
    flex: none;
  }
  .back-name {
    font-size: 52px;
    font-weight: 500;
    color: var(--card-white);
    line-height: 1;
  }
</style>
</head>
<body>
  <main class="canvas">
    <section class="card card-front" aria-label="Card front">
      <div class="brand-lockup">
        <span class="brand-dot"></span>
        <span class="brand-name">trelvo</span>
      </div>
      <p class="holder-name">MARA QUELLIN</p>
      <div class="contact">
        <div class="contact-labels">t<br>e</div>
        <div class="contact-values">555.018.2746<br>mara.quellin@trelvomail.net</div>
      </div>
    </section>

    <section class="card card-back" aria-label="Card back">
      <div class="back-mark">
        <span class="back-dot"></span>
        <span class="back-name">trelvo</span>
      </div>
    </section>
  </main>
</body>
</html>
```